Verdanith Website Concept

We would like a one page website. Please refer to the attached files for more information.

Please reference file attachment version 1.1.

```html
<!DOCTYPE html>
<html lang="en">
<head>
<meta charset="utf-8">
<title>Verdanith — Financial Security Company</title>
<link rel="stylesheet" href="https://fonts.googleapis.com/css2?family=Open+Sans:wght@300;400;600;700&display=swap">
<style>
:root{
  --navy:#3d4a85;
  --navy-dark:#2f3a6e;
  --band-top:#7e8bc0;
  --band-bottom:#4f5d98;
  --ink:#333;
  --muted:#a0a0a0;
  --body:#555;
  --grey-btn:#3c3c3c;
  --soft:#f1f1f1;
}
*{margin:0;padding:0;box-sizing:border-box}
html,body{width:827px;height:1200px;overflow:hidden}
body{font-family:'Open Sans',sans-serif;color:var(--ink);background:#fff;position:relative}
.abs{position:absolute}
h1,h2,h3{font-weight:400}

.hero-band{left:0;top:0;width:827px;height:324px;background:linear-gradient(180deg,var(--band-top),var(--band-bottom))}
.nav-bar{left:102px;top:22px;width:620px;height:55px;border-radius:6px;background:linear-gradient(180deg,#fdfdfd,#dcdcdc);box-shadow:0 2px 4px rgba(0,0,0,.25)}
.brand{left:16px;top:17px;display:flex;align-items:center;gap:7px;font-size:17px;color:var(--navy);letter-spacing:.5px}
.brand-mark{width:16px;height:16px;border-radius:50%;background:var(--navy)}
.nav-links{left:210px;top:20px;display:flex;gap:21px;font-size:10.5px;color:#222;list-style:none;white-space:nowrap;letter-spacing:-.2px}

.slider{left:102px;top:88px;width:620px;height:218px;background:#fff;border-radius:5px}
.slider-head{left:28px;top:86px;font-size:28px;line-height:29px;font-weight:300;color:var(--navy);letter-spacing:-.5px}
.slider-head strong{display:block;font-weight:600;color:#777}
.slider-photo{left:407px;top:0;width:158px;height:206px;background:linear-gradient(180deg,#ececec,#c9c5bd)}
.dots{left:288px;top:196px;display:flex;gap:3px}
.dots span{width:10px;height:10px;border-radius:50%;background:#c8c8c8}
.dots span:first-child{background:var(--navy)}

.services{left:0;top:324px;width:827px;height:332px;background:linear-gradient(180deg,#f2f2f2,#fff 60px)}
.section-title{font-size:11.5px;font-weight:600;color:var(--navy)}
.services .section-title{left:0;top:24px;width:837px;text-align:center}
.card{top:51px;width:152px}
.card-photo{width:150px;height:108px}
.card-title{margin-top:10px;height:32px;font-size:9px;line-height:16px;color:#333;font-weight:400;letter-spacing:-.1px}
.card-text{margin-top:6px;font-size:8px;line-height:15.7px;color:var(--muted);font-weight:300;letter-spacing:-.2px}
.btn-more{position:absolute;top:250px;left:0;background:var(--grey-btn);color:#fff;font-size:7.5px;font-weight:400;padding:3px 5px;letter-spacing:-.1px}

.company{left:0;top:656px;width:827px;height:470px;background:var(--soft)}
.company .section-title{left:103px;top:24px}
.company-photo{left:103px;top:46px;width:385px;height:148px;background:linear-gradient(180deg,#a9c6e6,#d4e0ea)}
.company-copy{left:103px;top:214px;width:392px;font-size:8.8px;line-height:15.7px;color:var(--body);letter-spacing:-.25px}
.company-copy p+p{margin-top:15.7px}
.btn-pill{left:103px;top:406px;width:60px;height:20px;border-radius:5px;background:var(--navy);color:#fff;font-size:9px;font-weight:700;text-align:center;line-height:20px}

.consult{left:521px;top:682px;width:202px;height:400px;border-radius:6px;background:linear-gradient(180deg,#5d6aa4,#4a5894)}
.consult h2{position:absolute;left:14px;top:14px;color:#fff;font-size:10px;line-height:12px}
.consult h2 span{display:block;font-size:15.5px;font-weight:600;line-height:20px}
.field{position:absolute;left:14px;width:175px;height:21px;border-radius:5px;background:#fff;border:1px solid #c9cbd8;font-size:8.6px;color:#777;padding:3px 6px;line-height:13px}
.field.tall{height:35px}
.field.msg{height:40px}
.submit{position:absolute;left:14px;top:370px;width:61px;height:21px;border-radius:5px;background:var(--navy-dark);color:#fff;font-size:9px;font-weight:700;text-align:center;line-height:21px}

.footer-links{left:102px;top:1142px;display:flex;font-size:9.6px;color:#333;list-style:none;white-space:nowrap}
.footer-links li+li::before{content:"|";margin:0 12px;color:#333}
.copyright{left:102px;top:1168px;font-size:9.6px;color:#444}
.social{left:660px;top:1152px;display:flex;gap:9px}
.social span{width:16px;height:16px;border-radius:50%;background:#555}
</style>
</head>
<body>

<div class="abs hero-band"></div>

<header class="abs nav-bar">
  <div class="abs brand"><span class="brand-mark"></span>Verdanith</div>
  <ul class="abs nav-links">
    <li>HOME</li><li>ABOUT US</li><li>SERVICES</li><li>WHY CHOOSE US</li><li>FAQ'S</li><li>CONTACT US</li>
  </ul>
</header>

<section class="abs slider">
  <h1 class="abs slider-head">We are a financial<strong>Security Company</strong></h1>
  <div class="abs slider-photo" role="img" aria-label="Photo: hand dropping a coin into a glass piggy bank"></div>
  <div class="abs dots"><span></span><span></span><span></span><span></span></div>
</section>

<section class="abs services">
  <h2 class="abs section-title">SERVICES WE OFFER</h2>

  <article class="abs card" style="left:103px">
    <div class="card-photo" role="img" aria-label="Photo: padlock icons on a digital screen" style="background:#2f5fb0"></div>
    <h3 class="card-title">Threat Assessment</h3>
    <p class="card-text">Lorem ipsum dolor sit amet, consectetur adipisicing elit, sed do eiusmod tempor incididunt ut labore et dolore magna aliqua. Ut enim ad minim</p>
    <span class="btn-more">READ MORE</span>
  </article>

  <article class="abs card" style="left:260px">
    <div class="card-photo" role="img" aria-label="Photo: filing drawer with folders" style="background:#a86a2c"></div>
    <h3 class="card-title">Threat Avoidance Plan<br>&amp; Dossier Creation</h3>
    <p class="card-text">Lorem ipsum dolor sit amet, consectetur adipisicing elit, sed do eiusmod tempor incididunt ut labore et dolore magna aliqua. Ut enim ad minim</p>
    <span class="btn-more">READ MORE</span>
  </article>

  <article class="abs card" style="left:416px">
    <div class="card-photo" role="img" aria-label="Photo: businessman holding a young plant" style="background:#2c2e33"></div>
    <h3 class="card-title">Elite Executive Protection</h3>
    <p class="card-text">Lorem ipsum dolor sit amet, consectetur adipisicing elit, sed do eiusmod tempor incididunt ut labore et dolore magna aliqua. Ut enim ad minim</p>
    <span class="btn-more">READ MORE</span>
  </article>

  <article class="abs card" style="left:572px">
    <div class="card-photo" role="img" aria-label="Photo: clasped hands resting on a wooden table" style="background:#9c8a76"></div>
    <h3 class="card-title">Threat Avoidance Plan<br>&amp; Dossier Maintenance</h3>
    <p class="card-text">Lorem ipsum dolor sit amet, consectetur adipisicing elit, sed do eiusmod tempor incididunt ut labore et dolore magna aliqua. Ut enim ad minim</p>
    <span class="btn-more">READ MORE</span>
  </article>
</section>

<section class="abs company">
  <h2 class="abs section-title">OUR COMPANY</h2>
  <div class="abs company-photo" role="img" aria-label="Photo: cupped hands holding coins with a green sprout"></div>
  <div class="abs company-copy">
    <p>Verdanith is a United States-based tier one security firm specializing inthe protection of financial services professionals, executives and their families. We manage engagements resulting from general and specific threats throughout the United States and abroad on behalf of our domestic clients. We deliver our services exclusively through associates and contractors with United States special operations, secret service, NIA, or equivalent experience and training. We are one of only a handful of domestic security firms that offers scalable, tier one security services in every market in the United States.</p>
    <p>If you have a general or specific threat you would like to have assessed, it will be our privilege to evaluate your circumstances and provide you with an opinion of how to best address your security needs. Not all security circumstances require tier one professionals.</p>
  </div>
  <div class="abs btn-pill">READ MORE</div>
</section>

<form class="abs consult">
  <h2>REQUEST FOR<span>CONSULTATION</span></h2>
  <div class="field" style="top:54px">First Name</div>
  <div class="field" style="top:80px">Last Name</div>
  <div class="field" style="top:106px">Home Phone</div>
  <div class="field" style="top:132px">Work Phone</div>
  <div class="field" style="top:158px">Cell Phone</div>
  <div class="field" style="top:184px">Email Address</div>
  <div class="field tall" style="top:209px">Address</div>
  <div class="field" style="top:247px">City</div>
  <div class="field" style="top:273px">State</div>
  <div class="field" style="top:298px">Zip</div>
  <div class="field msg" style="top:324px">Message</div>
  <div class="submit">SUBMIT</div>
</form>

<footer>
  <ul class="abs footer-links">
    <li>Home</li><li>About Us</li><li>Services</li><li>Why Choose Us</li><li>FAQ's</li><li>Contact Us</li>
  </ul>
  <p class="abs copyright">© 2014 | All rights reserved Verdanith, LLC...</p>
  <div class="abs social" aria-label="Social links"><span></span><span></span><span></span></div>
</footer>

</body>
</html>
```